Tide & Thistle Website Creation For Online Spirits Sales via MerrowVats.com

Want a Website developed that I will use to partner with Merrow Vats to sell my signature rum online. Merrow Vats will add the final code to make the website an e-commerce site. Website should have links to Social media pages, recipies, About, news and events, products. I have he domain name already just need a designer to make the website look professional. Need website capable of being viewed on iPhone and Android devices. Please use the color scheme that is on the label. The brand motto is: Celebrate Life With Family old and new friends. The bottle sent in the images will be replaced with and actual high resolution image of the bottle when it is produce on 27 DEC 21. Can give the selected designer access to develop the website. I have the hostbramble.com domain name. Final code will be added by a designer from MerrowVats.com to make it a e-commerce store.
Updates

I added more information to refine the design I wanted. I should have had this information available to the designers when I started the project.

Target Market(s)

Target Market is 25-50 year old who drink rum

Industry/Entity Type

Spirits. Using Website to sell Rum online

Number of Pages Required

1 page

Font styles to use
Sans Serif

Colors
00AB8E
00BBA5
67D7C9
C6EFE9
E9F9F6

Requirements
Must have
• Must look elegant and of high class. Rum is being market as a premium unnamed rum.
Nice to have
• Video of people drinking, smiling and celebrating

```html
<!DOCTYPE html>
<html lang="en">
<head>
<meta charset="utf-8">
<title>Tide &amp; Thistle — Homepage Layouts</title>
<link rel="stylesheet" href="https://fonts.googleapis.com/css2?family=Cinzel:wght@500;600;700&family=Roboto:wght@400;500;700&display=swap">
<style>
:root{
  --stage:#a9aaac;
  --paper:#e9e3cb;
  --paper-light:#efe9d3;
  --paper-deep:#ddd6bb;
  --green:#149474;
  --green-dark:#0f7c61;
  --ink:#1b1b1b;
  --text:#3a3a3a;
  --muted:#6b6b6b;
  --white:#ffffff;
  --gold:#f29a1a;
}
*{box-sizing:border-box;margin:0;padding:0}
html,body{width:791px;height:1200px;overflow:hidden}
body{background:var(--stage);font-family:"Roboto",sans-serif;color:var(--text);position:relative}
.page{position:absolute;top:49px;width:314px;height:1102px;background:radial-gradient(ellipse at 50% 30%,var(--paper-light) 0%,var(--paper) 60%,#e2dbc0 100%);overflow:hidden;box-shadow:0 2px 8px rgba(0,0,0,.18)}
.page--fields{left:55px}
.page--cane{left:415px}
.abs{position:absolute}
.display{font-family:"Cinzel",serif;font-weight:600;color:var(--ink);letter-spacing:.5px;line-height:1}
.btn{position:absolute;background:var(--green);color:var(--white);border-radius:8px;font-weight:700;display:flex;align-items:center;justify-content:center;gap:2.5px;white-space:nowrap;box-shadow:0 1px 2px rgba(0,0,0,.15)}
.arrow-dot{display:inline-block;width:3.6px;height:3.6px;border-radius:50%;background:var(--white)}

/* top bar + header */
.topbar{left:0;top:0;width:314px;height:10px;background:var(--ink);color:var(--white);font-size:3px;display:flex;align-items:center;justify-content:center}
.header{left:0;top:10px;width:314px;height:22px;background:var(--paper)}
.brand{left:29px;top:7px;display:flex;align-items:center;gap:2.5px;font-family:"Cinzel",serif;font-size:4.6px;font-weight:600;color:var(--ink)}
.brand-dot{width:8px;height:8px;border-radius:50%;background:var(--ink)}
.nav{left:90px;top:9px;display:flex;gap:6.5px;font-size:3.8px;color:var(--ink);font-weight:500}
.btn--club{left:212px;top:6px;width:39px;height:10px;font-size:3.8px;font-weight:500;border-radius:6px}
.icons{left:256px;top:9px;display:flex;gap:4px}
.icons span{width:3.5px;height:3.5px;background:var(--ink);border-radius:1px}

/* hero */
.hero{left:0;top:32px;width:314px;height:155px}
.page--fields .hero{background:linear-gradient(172deg,#7d9bb5 0%,#b9bcae 20%,#e6bd7d 33%,#a49a4c 41%,#5f8128 52%,#3f6a1d 70%,#23420f 100%)}
.page--cane .hero{background:linear-gradient(90deg,#1d1a26 0%,#3a3145 15%,#57504f 32%,#9c9676 48%,#b7ad8a 52%,#5e5650 66%,#372f42 84%,#1b1824 100%)}
.hero-edge{left:0;top:178px;width:314px;height:12px}
.hero-title{left:29px;top:73px;font-size:10.5px;line-height:12.6px;color:var(--white);text-shadow:0 1px 2px rgba(0,0,0,.35)}
.hero-title em{font-style:normal;color:#1fa581}
.hero-copy{left:29px;top:113px;width:136px;font-size:4.2px;line-height:7px;color:var(--white);text-shadow:0 1px 1px rgba(0,0,0,.4)}
.btn--shop{left:29px;top:136px;width:49px;height:12px;font-size:4px}
.bottle{border-radius:9px 9px 12px 12px;background:linear-gradient(90deg,#6e3a0c 0%,#a9651a 18%,#d9a048 36%,#f0c679 44%,#c9852a 60%,#93541a 82%,#5e300a 100%);box-shadow:3px 6px 8px rgba(0,0,0,.35)}
.page--fields .hero-bottle{left:185px;top:85px;width:37px;height:113px}
.page--cane .hero-bottle{left:212px;top:52px;width:52px;height:151px}

/* about */
.about-visual{left:30px;top:217px;width:109px;height:109px;border-radius:50%;background:radial-gradient(circle at 45% 40%,#8d8f6a 0%,#5d6444 40%,#3a3d2c 75%,#26261f 100%);border:5px solid var(--paper-light);box-shadow:0 0 0 1.6px #34352c,0 3px 6px rgba(0,0,0,.2)}
.about-title{left:155px;top:229px;font-size:10.5px}
.about-copy{left:155px;top:245px;width:131px;font-size:3.5px;line-height:6.7px;color:var(--muted)}
.about-copy p+p{margin-top:2.5px}
.btn--more{left:155px;top:303px;width:45px;height:11px;font-size:3.6px}

.section-title{left:0;width:314px;text-align:center;font-size:10px}

/* cards */
.card{position:absolute;width:81px;background:var(--white);border-radius:3px;box-shadow:0 2px 5px rgba(0,0,0,.14);text-align:center;overflow:hidden}
.card-img{width:100%;height:55px}
.card h3{font-size:4.6px;font-weight:700;color:var(--ink);margin-top:6px}
.card p{font-size:3.4px;line-height:6px;color:var(--muted);padding:2.5px 5px 0}
.recipe{top:370px;height:96px}
.img-sunset{background:linear-gradient(180deg,#f1d7a5 0%,#e2a866 35%,#b06f33 62%,#4f3420 100%)}
.img-toast{background:linear-gradient(180deg,#9aa08c 0%,#6e6a5b 35%,#8b6a4d 65%,#2f2924 100%)}
.img-friends{background:linear-gradient(180deg,#a7b58c 0%,#8e9b78 35%,#c7a79a 70%,#6b6a78 100%)}

/* testimonials */
.band{left:0;top:508px;width:314px;height:117px;background:linear-gradient(180deg,#16977a,var(--green) 60%,#128c6e)}
.band-title{left:0;top:520px;width:314px;text-align:center;font-size:9.5px;color:var(--paper)}
.quote-card{position:absolute;top:540px;width:107px;height:61px;background:var(--white);border-radius:8px;box-shadow:0 2px 5px rgba(0,0,0,.22)}
.quote-mark{position:absolute;left:26px;top:5px;font-family:"Cinzel",serif;font-size:14px;font-weight:700;color:var(--green);line-height:1}
.quote-text{position:absolute;left:26px;top:18px;width:76px;font-size:3.4px;line-height:6.2px;color:var(--muted)}
.quote-name{position:absolute;left:26px;top:42px;font-size:4.2px;font-weight:500;color:var(--ink)}
.stars{display:flex;gap:.6px}
.stars span{width:3px;height:3px;background:var(--gold);clip-path:polygon(50% 0,61% 35%,98% 35%,68% 57%,79% 91%,50% 70%,21% 91%,32% 57%,2% 35%,39% 35%)}
.quote-stars{position:absolute;left:26px;top:49px}
.avatar{position:absolute;top:555px;width:30px;height:30px;border-radius:50%;background:radial-gradient(circle at 50% 35%,#c9c2b8 0%,#8a8680 45%,#3c4450 100%);border:1.5px solid var(--white);box-shadow:0 1px 3px rgba(0,0,0,.25)}
.chev{top:564px;width:12px;height:12px}

/* product */
.product-media{left:30px;top:672px;width:111px;height:127px;background:linear-gradient(180deg,#7fd3b8 0%,#4bb695 40%,#2b9a7a 75%,#3da889 100%)}
.product-bottle{left:66px;top:682px;width:37px;height:112px}
.play{left:77px;top:720px;width:15px;height:15px;border-radius:50%;background:var(--green);box-shadow:0 1px 3px rgba(0,0,0,.3)}
.play::after{content:"";position:absolute;left:5.5px;top:3.8px;border-left:5.5px solid var(--white);border-top:3.7px solid transparent;border-bottom:3.7px solid transparent}
.thumb{top:804px;width:34px;height:23px}
.thumb-a{background:linear-gradient(135deg,#4b1e1e,#7a3a2c 50%,#2a1612)}
.thumb-b{background:linear-gradient(90deg,#f0ece4,#6b1a1a 30%,#e9e4da 55%,#5a1515 80%,#efeae0)}
.thumb-c{background:linear-gradient(135deg,#1c1614,#5b2020 55%,#241a18)}
.p-tag{left:151px;top:671px;font-size:3.5px;color:var(--muted)}
.p-name{left:150px;top:676px;font-size:8px;font-weight:500;color:var(--ink)}
.p-stars{left:151px;top:687px;display:flex;align-items:center;gap:1px;font-size:2.6px;color:var(--muted)}
.p-price{left:151px;top:693px;font-size:6px;font-weight:500;color:var(--green)}
.p-label{left:151px;top:710px;font-size:4.2px;font-weight:500;color:var(--ink)}
.p-select{left:151px;top:718px;width:129px;height:15px;background:#f4f1e7;border:.5px solid #d9d3be;font-size:3.4px;color:var(--muted);display:flex;align-items:center;justify-content:space-between;padding:0 6px}
.p-list{left:151px;top:743px;list-style:none;font-size:3.5px;line-height:7.4px;color:var(--muted)}
.p-list li{display:flex;align-items:center;gap:4px}
.tick{width:3.4px;height:3.4px;border-radius:50%;background:var(--green)}
.p-review{left:151px;top:773px;width:129px;height:23px;background:var(--white);border-radius:12px;display:flex;align-items:center;gap:6px;padding:0 4px;font-size:3.4px;line-height:6.2px;color:var(--muted)}
.p-review .mini-avatar{flex:none;width:16px;height:16px;border-radius:50%;background:radial-gradient(circle at 50% 35%,#c7b8a8,#6a5a50 60%,#3a3230)}
.btn--cart{left:163px;top:812px;width:113px;height:15px;font-size:4.8px;font-weight:500}

/* blog */
.blog-band{left:0;top:927px;width:314px;height:81px;background:var(--paper-deep)}
.post{top:877px;height:101px}
.post .card-img{width:75px;height:53px;margin:3px 3px 0}
.img-fire{background:linear-gradient(180deg,#6c7e8e 0%,#5a6470 40%,#a4602c 70%,#e5842e 100%)}
.img-table{background:linear-gradient(180deg,#c2c58c 0%,#8c9a5a 35%,#6a5a44 70%,#3c3026 100%)}
.img-hills{background:linear-gradient(180deg,#e4d2a8 0%,#c9ae7c 35%,#8d8456 65%,#5a5844 100%)}
.post .date{font-size:3.3px;color:var(--green);margin-top:6px}
.post h3{margin-top:2px}
.post .read{display:block;font-size:3.8px;font-weight:700;color:var(--green);margin-top:3px}

/* footer */
.footer{left:0;top:1008px;width:314px;height:94px;background:var(--ink)}
.f-col{color:#e6e6e6}
.f-head{font-size:4.8px;font-weight:500;color:var(--white)}
.f-col1{left:29px;top:1024px;width:80px}
.f-contact{list-style:none;font-size:3.5px;line-height:6px;margin-top:7px}
.f-contact li{display:flex;gap:4px;margin-bottom:3.4px}
.f-contact i{flex:none;width:3px;height:3px;border-radius:50%;background:var(--green);margin-top:1.5px}
.f-col2{left:113px;top:1024px}
.f-links{display:flex;gap:12px;margin-top:7px;font-size:3.5px;line-height:7px}
.f-col3{left:186px;top:1024px;width:100px}
.f-form{display:flex;gap:4px;margin-top:5px}
.f-input{width:62px;height:11px;border-radius:6px;background:var(--white);color:var(--muted);font-size:3px;display:flex;align-items:center;padding-left:6px}
.f-submit{width:32px;height:11px;border-radius:6px;background:var(--green);color:var(--white);font-size:4px;font-weight:700;display:flex;align-items:center;justify-content:center}
.f-check{font-size:3.2px;margin-top:7px}
.f-social{display:flex;gap:3px;margin-top:7px}
.f-social span{width:8px;height:8px;border-radius:50%;border:.5px solid var(--white)}
.copyright{left:0;top:1090px;width:314px;text-align:center;font-size:3.4px;color:#e6e6e6}
</style>
</head>
<body>

<!-- Layout A: field hero -->
<section class="page page--fields">
  <div class="abs topbar">Lorem ipsum dolor sit amet, consectetur adipiscing</div>
  <header class="abs header">
    <div class="abs brand"><span class="brand-dot"></span>TIDE &amp; THISTLE</div>
    <nav class="abs nav"><span>Home</span><span>Shop</span><span>Gifts</span><span>Bottle Shop</span><span>Blog</span><span>Contact Us</span></nav>
    <div class="btn btn--club">Subscribe Club</div>
    <div class="abs icons"><span></span><span></span><span></span><span></span></div>
  </header>
  <div class="abs hero" role="img" aria-label="Photo of green sugarcane fields under a sunset sky"></div>
  <svg class="abs hero-edge" viewBox="0 0 314 12" preserveAspectRatio="none"><path d="M0 6 Q20 2 40 6 T80 5 T120 7 T160 4 T200 6 T240 5 T280 7 T314 5 V12 H0Z" fill="#e9e3cb"/></svg>
  <h1 class="abs display hero-title">CELEBRATE LIFE WITH<br>FAMILY, <em>OLD AND<br>NEW FRIENDS</em></h1>
  <p class="abs hero-copy">Lorem ipsum dolor sit amet, consectetur adipiscing elit, sed do tempor incididunt ut labore et dolore magna aliqua.</p>
  <div class="btn btn--shop">SHOP NOW <span class="arrow-dot"></span></div>
  <div class="abs bottle hero-bottle" role="img" aria-label="Photo of a bottle of Tide &amp; Thistle rum"></div>

  <div class="abs about-visual" role="img" aria-label="Round photo of a rum bottle among cane leaves"></div>
  <h2 class="abs display about-title">ABOUT US</h2>
  <div class="abs about-copy">
    <p>Lorem ipsum dolor sit amet, consectetur adipiscing elit, sed do eiusmod tempor incididunt ut labore et dolore magna aliqua. Ut enim ad minim veniam, quis nostrud exercitation ullamco laboris nisi ut aliquip ex ea commodo consequat.</p>
    <p>Duis aute irure dolor in reprehenderit in voluptate velit esse cillum dolore eu fugiat nulla pariatur. Excepteur sint occaecat cupidatat non proident, sunt in culpa qui officia deserunt mollit anim id est laborum.</p>
  </div>
  <div class="btn btn--more">READ MORE <span class="arrow-dot"></span></div>

  <h2 class="abs display section-title" style="top:349px">OUR RECIPES</h2>
  <article class="card recipe" style="left:30px"><div class="card-img img-sunset" role="img" aria-label="Photo of an outdoor dinner at sunset"></div><h3>Lorem ipsum dolor sit amet,</h3><p>Sed ut perspiciatis unde omnis iste natus error sit voluptatem accusantium doloremque laudantium,</p></article>
  <article class="card recipe" style="left:117px"><div class="card-img img-toast" role="img" aria-label="Photo of friends raising glasses at a table"></div><h3>Lorem ipsum dolor sit amet,</h3><p>Sed ut perspiciatis unde omnis iste natus error sit voluptatem accusantium doloremque laudantium,</p></article>
  <article class="card recipe" style="left:204px"><div class="card-img img-friends" role="img" aria-label="Photo of two women sharing drinks outdoors"></div><h3>Lorem ipsum dolor sit amet,</h3><p>Sed ut perspiciatis unde omnis iste natus error sit voluptatem accusantium doloremque laudantium,</p></article>

  <div class="abs band"></div>
  <h2 class="abs display band-title">CLIENTS TESTIMONIAL</h2>
  <svg class="abs chev" style="left:8px" viewBox="0 0 12 12"><path d="M8 2 4 6l4 4" fill="none" stroke="#cfe8df" stroke-width="1"/></svg>
  <svg class="abs chev" style="left:294px" viewBox="0 0 12 12"><path d="M4 2l4 4-4 4" fill="none" stroke="#cfe8df" stroke-width="1"/></svg>
  <div class="quote-card" style="left:48px"><span class="quote-mark">“</span><p class="quote-text">Sed ut perspiciatis unde omnis iste natus sit voluptatem accusantium doloremque laudantium, totam rem aperiam,</p><span class="quote-name">John Doe</span><div class="stars quote-stars"><span></span><span></span><span></span><span></span><span></span></div></div>
  <div class="quote-card" style="left:176px"><span class="quote-mark">“</span><p class="quote-text">Sed ut perspiciatis unde omnis iste natus sit voluptatem accusantium doloremque laudantium, totam rem aperiam,</p><span class="quote-name">John Doe</span><div class="stars quote-stars"><span></span><span></span><span></span><span></span><span></span></div></div>
  <div class="avatar" style="left:35px" role="img" aria-label="Customer portrait"></div>
  <div class="avatar" style="left:163px" role="img" aria-label="Customer portrait"></div>

  <h2 class="abs display section-title" style="top:648px">OUR PRODUCTS</h2>
  <div class="abs product-media" role="img" aria-label="Video still of the rum bottle in a cane grove"></div>
  <div class="abs bottle product-bottle" role="img" aria-label="Rum bottle"></div>
  <div class="abs play"></div>
  <div class="abs thumb thumb-a" style="left:30px" role="img" aria-label="Video thumbnail"></div>
  <div class="abs thumb thumb-b" style="left:68px" role="img" aria-label="Photo of bottles on a shelf"></div>
  <div class="abs thumb thumb-c" style="left:107px" role="img" aria-label="Photo of a bottle close-up"></div>
  <span class="abs p-tag">NEW ARRIVAL</span>
  <h3 class="abs p-name">Lorem ipsum dolor sit amet,</h3>
  <div class="abs p-stars"><div class="stars"><span></span><span></span><span></span><span></span><span></span></div>(25 Customer Reviews)</div>
  <span class="abs p-price">$149.94</span>
  <span class="abs p-label">Quantity</span>
  <div class="abs p-select">Choose Qty <span>⇕</span></div>
  <ul class="abs p-list"><li><i class="tick"></i>Sed ut perspiciatis unde omnis iste natus</li><li><i class="tick"></i>Accusantium doloremque laudantium,</li><li><i class="tick"></i>Totam rem aperiam, eaque ipsa quae ab illo</li></ul>
  <div class="abs p-review"><span class="mini-avatar" role="img" aria-label="Reviewer portrait"></span><p>“ Lorem ipsum dolor sit amet, consectetur adipiscing elit, sed do eiusmod tempor incididunt ut labore et dolore magna aliqua. nostrud exercitation ”</p></div>
  <div class="btn btn--cart">ADD TO CART</div>

  <div class="abs blog-band"></div>
  <h2 class="abs display section-title" style="top:858px">OUR BLOG</h2>
  <article class="card post" style="left:30px"><div class="card-img img-fire" role="img" aria-label="Photo of friends by a campfire"></div><p class="date">February 2, 2021</p><h3>Lorem ipsum dolor sit amet,</h3><p>Sed ut perspiciatis unde omnis iste natus sit voluptatem accusantium</p><span class="read">READ MORE ›</span></article>
  <article class="card post" style="left:117px"><div class="card-img img-table" role="img" aria-label="Photo of friends toasting at an outdoor table"></div><p class="date">February 2, 2021</p><h3>Lorem ipsum dolor sit amet,</h3><p>Sed ut perspiciatis unde omnis iste natus sit voluptatem accusantium</p><span class="read">READ MORE ›</span></article>
  <article class="card post" style="left:204px"><div class="card-img img-hills" role="img" aria-label="Photo of two women sharing drinks in the hills"></div><p class="date">February 2, 2021</p><h3>Lorem ipsum dolor sit amet,</h3><p>Sed ut perspiciatis unde omnis iste natus sit voluptatem accusantium</p><span class="read">READ MORE ›</span></article>

  <footer class="abs footer"></footer>
  <div class="abs f-col f-col1"><h4 class="f-head">Contact Us</h4><ul class="f-contact"><li><i></i>Lorem ipsum dolor sit consectetur adipiscing elit</li><li><i></i>info@tideandthistle.com</li><li><i></i>555-014-2290</li><li><i></i>1 (555) 010 - 4471</li></ul></div>
  <div class="abs f-col f-col2"><h4 class="f-head">Links</h4><div class="f-links"><div>Home<br>Shop<br>Products<br>About Us<br>Blog<br>Offers</div><div>Terms &amp; Condition<br>Privacy Policy<br>Support<br>Site Map<br>Contact Us</div></div></div>
  <div class="abs f-col f-col3"><h4 class="f-head">Subscribe for Updates</h4><div class="f-form"><div class="f-input">Emaill Address</div><div class="f-submit">SUBMIT</div></div><p class="f-check">☑ Yes, Please Contact me.</p><div class="f-social"><span></span><span></span><span></span></div></div>
  <p class="abs copyright">© 2021 Tide &amp; Thistle | All Rights Reserved</p>
</section>

<!-- Layout B: cane grove hero -->
<section class="page page--cane">
  <div class="abs topbar">Lorem ipsum dolor sit amet, consectetur adipiscing</div>
  <header class="abs header">
    <div class="abs brand"><span class="brand-dot"></span>TIDE &amp; THISTLE</div>
    <nav class="abs nav"><span>Home</span><span>Shop</span><span>Gifts</span><span>Bottle Shop</span><span>Blog</span><span>Contact Us</span></nav>
    <div class="btn btn--club">Subscribe Club</div>
    <div class="abs icons"><span></span><span></span><span></span><span></span></div>
  </header>
  <div class="abs hero" role="img" aria-label="Photo of a path between rows of dark sugarcane"></div>
  <svg class="abs hero-edge" viewBox="0 0 314 12" preserveAspectRatio="none"><path d="M0 6 Q20 2 40 6 T80 5 T120 7 T160 4 T200 6 T240 5 T280 7 T314 5 V12 H0Z" fill="#e9e3cb"/></svg>
  <h1 class="abs display hero-title">CELEBRATE LIFE WITH<br>FAMILY, <em>OLD AND<br>NEW FRIENDS</em></h1>
  <p class="abs hero-copy">Lorem ipsum dolor sit amet, consectetur adipiscing elit, sed do tempor incididunt ut labore et dolore magna aliqua.</p>
  <div class="btn btn--shop">SHOP NOW <span class="arrow-dot"></span></div>
  <div class="abs bottle hero-bottle" role="img" aria-label="Photo of a bottle of Tide &amp; Thistle rum"></div>

  <div class="abs about-visual" role="img" aria-label="Round photo of a rum bottle among cane leaves"></div>
  <h2 class="abs display about-title">ABOUT US</h2>
  <div class="abs about-copy">
    <p>Lorem ipsum dolor sit amet, consectetur adipiscing elit, sed do eiusmod tempor incididunt ut labore et dolore magna aliqua. Ut enim ad minim veniam, quis nostrud exercitation ullamco laboris nisi ut aliquip ex ea commodo consequat.</p>
    <p>Duis aute irure dolor in reprehenderit in voluptate velit esse cillum dolore eu fugiat nulla pariatur. Excepteur sint occaecat cupidatat non proident, sunt in culpa qui officia deserunt mollit anim id est laborum.</p>
  </div>
  <div class="btn btn--more">READ MORE <span class="arrow-dot"></span></div>

  <h2 class="abs display section-title" style="top:349px">OUR RECIPES</h2>
  <article class="card recipe" style="left:30px"><div class="card-img img-sunset" role="img" aria-label="Photo of an outdoor dinner at sunset"></div><h3>Lorem ipsum dolor sit amet,</h3><p>Sed ut perspiciatis unde omnis iste natus error sit voluptatem accusantium doloremque laudantium,</p></article>
  <article class="card recipe" style="left:117px"><div class="card-img img-toast" role="img" aria-label="Photo of friends raising glasses at a table"></div><h3>Lorem ipsum dolor sit amet,</h3><p>Sed ut perspiciatis unde omnis iste natus error sit voluptatem accusantium doloremque laudantium,</p></article>
  <article class="card recipe" style="left:204px"><div class="card-img img-friends" role="img" aria-label="Photo of two women sharing drinks outdoors"></div><h3>Lorem ipsum dolor sit amet,</h3><p>Sed ut perspiciatis unde omnis iste natus error sit voluptatem accusantium doloremque laudantium,</p></article>

  <div class="abs band"></div>
  <h2 class="abs display band-title">CLIENTS TESTIMONIAL</h2>
  <svg class="abs chev" style="left:8px" viewBox="0 0 12 12"><path d="M8 2 4 6l4 4" fill="none" stroke="#cfe8df" stroke-width="1"/></svg>
  <svg class="abs chev" style="left:294px" viewBox="0 0 12 12"><path d="M4 2l4 4-4 4" fill="none" stroke="#cfe8df" stroke-width="1"/></svg>
  <div class="quote-card" style="left:48px"><span class="quote-mark">“</span><p class="quote-text">Sed ut perspiciatis unde omnis iste natus sit voluptatem accusantium doloremque laudantium, totam rem aperiam,</p><span class="quote-name">John Doe</span><div class="stars quote-stars"><span></span><span></span><span></span><span></span><span></span></div></div>
  <div class="quote-card" style="left:176px"><span class="quote-mark">“</span><p class="quote-text">Sed ut perspiciatis unde omnis iste natus sit voluptatem accusantium doloremque laudantium, totam rem aperiam,</p><span class="quote-name">John Doe</span><div class="stars quote-stars"><span></span><span></span><span></span><span></span><span></span></div></div>
  <div class="avatar" style="left:35px" role="img" aria-label="Customer portrait"></div>
  <div class="avatar" style="left:163px" role="img" aria-label="Customer portrait"></div>

  <h2 class="abs display section-title" style="top:648px">OUR PRODUCTS</h2>
  <div class="abs product-media" role="img" aria-label="Video still of the rum bottle in a cane grove"></div>
  <div class="abs bottle product-bottle" role="img" aria-label="Rum bottle"></div>
  <div class="abs play"></div>
  <div class="abs thumb thumb-a" style="left:30px" role="img" aria-label="Video thumbnail"></div>
  <div class="abs thumb thumb-b" style="left:68px" role="img" aria-label="Photo of bottles on a shelf"></div>
  <div class="abs thumb thumb-c" style="left:107px" role="img" aria-label="Photo of a bottle close-up"></div>
  <span class="abs p-tag">NEW ARRIVAL</span>
  <h3 class="abs p-name">Lorem ipsum dolor sit amet,</h3>
  <div class="abs p-stars"><div class="stars"><span></span><span></span><span></span><span></span><span></span></div>(25 Customer Reviews)</div>
  <span class="abs p-price">$149.94</span>
  <span class="abs p-label">Quantity</span>
  <div class="abs p-select">Choose Qty <span>⇕</span></div>
  <ul class="abs p-list"><li><i class="tick"></i>Sed ut perspiciatis unde omnis iste natus</li><li><i class="tick"></i>Accusantium doloremque laudantium,</li><li><i class="tick"></i>Totam rem aperiam, eaque ipsa quae ab illo</li></ul>
  <div class="abs p-review"><span class="mini-avatar" role="img" aria-label="Reviewer portrait"></span><p>“ Lorem ipsum dolor sit amet, consectetur adipiscing elit, sed do eiusmod tempor incididunt ut labore et dolore magna aliqua. nostrud exercitation ”</p></div>
  <div class="btn btn--cart">ADD TO CART</div>

  <div class="abs blog-band"></div>
  <h2 class="abs display section-title" style="top:858px">OUR BLOG</h2>
  <article class="card post" style="left:30px"><div class="card-img img-fire" role="img" aria-label="Photo of friends by a campfire"></div><p class="date">February 2, 2021</p><h3>Lorem ipsum dolor sit amet,</h3><p>Sed ut perspiciatis unde omnis iste natus sit voluptatem accusantium</p><span class="read">READ MORE ›</span></article>
  <article class="card post" style="left:117px"><div class="card-img img-table" role="img" aria-label="Photo of friends toasting at an outdoor table"></div><p class="date">February 2, 2021</p><h3>Lorem ipsum dolor sit amet,</h3><p>Sed ut perspiciatis unde omnis iste natus sit voluptatem accusantium</p><span class="read">READ MORE ›</span></article>
  <article class="card post" style="left:204px"><div class="card-img img-hills" role="img" aria-label="Photo of two women sharing drinks in the hills"></div><p class="date">February 2, 2021</p><h3>Lorem ipsum dolor sit amet,</h3><p>Sed ut perspiciatis unde omnis iste natus sit voluptatem accusantium</p><span class="read">READ MORE ›</span></article>

  <footer class="abs footer"></footer>
  <div class="abs f-col f-col1"><h4 class="f-head">Contact Us</h4><ul class="f-contact"><li><i></i>Lorem ipsum dolor sit consectetur adipiscing elit</li><li><i></i>info@tideandthistle.com</li><li><i></i>555-014-2290</li><li><i></i>1 (555) 010 - 4471</li></ul></div>
  <div class="abs f-col f-col2"><h4 class="f-head">Links</h4><div class="f-links"><div>Home<br>Shop<br>Products<br>About Us<br>Blog<br>Offers</div><div>Terms &amp; Condition<br>Privacy Policy<br>Support<br>Site Map<br>Contact Us</div></div></div>
  <div class="abs f-col f-col3"><h4 class="f-head">Subscribe for Updates</h4><div class="f-form"><div class="f-input">Emaill Address</div><div class="f-submit">SUBMIT</div></div><p class="f-check">☑ Yes, Please Contact me.</p><div class="f-social"><span></span><span></span><span></span></div></div>
  <p class="abs copyright">© 2021 Tide &amp; Thistle | All Rights Reserved</p>
</section>

</body>
</html>
```